Events publishing website

Have increased the budget for Coded website design. Thanks
-
We need a wordpress website for events publishing. The website will be using all different kinds of events (social, business, music etc). The website should allow user to submit the new events. the new events will be published after admin reviewed.
Key menu items & requirements
- New Events (1-show picture, short description & start/end date. User can view more details in another page. 2-have categories, such as locations, free/ticked, event type etc. 3 - allow user to share the events in social website)
- Event organizer list (show the full list and most popular event organizers. users can view the list by categories, similar to above)
- events establishments (allow user to publish events related informations such as equipments, venue informations etc)
- discussion forum
Key functions
-registration page (new users should fill name, location, normal users or event organizer, types of event organizer etc)
-allow user to change locations to view different events
-search function
The functions should be similar to the following, the design should not. The website should not look like a proper website.
http://www.plavorgatherings.example
Reason: Hi All, have extended few days to allow some changes to be made for current design. Thanks

```html
<!DOCTYPE html>
<html lang="en">
<head>
<meta charset="utf-8">
<title>Events – Event Publishing</title>
<link href="https://fonts.googleapis.com/css2?family=Source+Sans+3:wght@400;600&display=swap" rel="stylesheet">
<style>
:root{
  --page-bg:#ecebe5;
  --topbar:#111;
  --teal:#3f7f76;
  --teal-dark:#2f655d;
  --teal-light:#5c958c;
  --orange:#f39c12;
  --orange-dark:#e28a05;
  --text:#222;
  --link:#1f6b63;
  --panel:#ffffff;
  --head-bg:#e6eeed;
}
*{box-sizing:border-box;margin:0;padding:0}
html,body{width:1200px;height:2699px;overflow:hidden}
body{
  position:relative;
  font-family:"Source Sans 3",Arial,sans-serif;
  color:var(--text);
  background:radial-gradient(circle at 300px 200px,#ffffff 0,#f3f2ed 500px,var(--page-bg) 1100px);
}
.abs{position:absolute}

.top-bar{position:absolute;left:0;top:0;width:1200px;height:36px;background:var(--topbar);color:#fff;font-size:12.5px;font-weight:600;display:flex;align-items:center;padding-left:34px;letter-spacing:.2px}
.top-bar span{padding:0 11px;border-right:1px solid #888;line-height:12px}
.top-bar span:first-child{padding-left:0}
.top-bar span:last-child{border:none}

.brand{left:46px;top:74px;color:var(--teal);font-size:44px;line-height:1}
.slogan{left:48px;top:118px;color:#8a8a2e;font-size:17px}
.account{right:56px;top:62px;display:flex;gap:24px;color:var(--teal-dark);font-size:16px}
.account span{display:flex;align-items:center;gap:6px}
.search{left:835px;top:112px;width:338px;height:38px;display:flex}
.search .field{flex:1;background:#fff;border:1px solid #d3d3d3;font-size:14px;color:#888;padding:9px 12px}
.search .go{width:41px;background:var(--orange);color:#fff;font-size:14px;display:flex;align-items:center;justify-content:center}

.main-nav{left:35px;top:172px;width:1145px;height:63px;background:linear-gradient(#4d8d83,var(--teal-dark));display:flex;padding-left:18px;box-shadow:0 2px 3px rgba(0,0,0,.25)}
.main-nav a{color:#fff;font-size:19px;padding:0 22px;display:flex;align-items:center;border-right:1px solid rgba(255,255,255,.35)}

.hero{left:35px;top:235px;width:1145px;height:361px;background:linear-gradient(90deg,#2a2e3b 0%,#6c7592 20%,#3b2b20 45%,#7a3a1a 70%,#d7681d 85%,#4a2513 100%)}
.hero-shade{left:35px;top:420px;width:1145px;height:176px;background:linear-gradient(rgba(0,0,0,0),rgba(40,20,10,.55))}
.slider-arrow{top:380px;width:44px;height:44px;border-radius:50%;background:#f1f1f1;border:1px solid #ccc;color:#999;font-size:26px;display:flex;align-items:center;justify-content:center}

.filter-bar{left:46px;top:604px;width:789px;height:52px;background:var(--orange);display:flex;align-items:center;padding:0 16px;color:#fff;font-size:19px;gap:8px}
.filter-bar .pill{height:24px;background:#fff;border-radius:12px;margin-right:14px}
.filter-bar .go{background:var(--orange-dark);border:1px solid #f7c063;width:52px;height:30px;display:flex;align-items:center;justify-content:center;font-size:16px;margin-left:auto}

.event-list{left:46px;top:656px;width:789px;height:1655px;background:var(--panel);border:1px solid #ddd;border-top:none}
.total{left:18px;top:20px;font-size:19px}
.event{position:absolute;left:16px;width:760px;height:200px}
.thumb{position:absolute;left:0;top:0;width:241px;height:176px;border:5px solid #fff;box-shadow:0 0 3px rgba(0,0,0,.45)}
.event-body{position:absolute;left:264px;top:0;width:490px}
.event-title{font-size:19px;line-height:24px;margin-bottom:4px;font-weight:400}
.event-desc{font-size:13.5px;line-height:18px;color:#333;margin-bottom:10px}
.event-meta{font-size:13.5px;line-height:25px;color:#333}
.share{display:flex;align-items:center;gap:6px;font-size:13.5px;margin-top:4px}
.share i{display:inline-block;width:24px;height:24px;border-radius:4px;margin-left:2px}
.share .s1{background:#4aa6df}.share .s2{background:#2f74ae}.share .s3{background:#3b5b99}
.separator{position:absolute;left:0;width:789px;border-top:1px dashed #aaa}
.pager-line{left:26px;top:1596px;width:740px;border-top:1px solid #cfdedc}
.pager{right:26px;top:1607px;display:flex;align-items:center;gap:10px;font-size:15px}
.pager .current{width:24px;height:24px;border-radius:50%;background:var(--teal);color:#fff;display:flex;align-items:center;justify-content:center}

.sidebar{left:847px;top:604px;width:326px;height:1711px;background:var(--panel);border:1px solid #ddd}
.side-head{position:absolute;left:0;width:324px;height:44px;background:linear-gradient(#f3f7f6,var(--head-bg));color:var(--teal-dark);font-size:21px;padding:9px 16px;border-bottom:1px solid #d6e0de}
.side-img{position:absolute;left:15px;width:293px;height:130px;border:4px solid #fff;box-shadow:0 0 3px rgba(0,0,0,.4)}
.side-event{position:absolute;left:15px;width:295px}
.side-event h4{font-size:16px;font-weight:400;color:var(--teal-dark)}
.side-event .when{font-size:12.5px;margin:3px 0 6px}
.side-event p{font-size:12.5px;line-height:21px;color:#444}
.side-event .more{font-size:13.5px;color:var(--teal-dark);margin-top:8px}
.edit-view{position:absolute;right:18px;font-size:12.5px;color:#555}
.organizer-photo{left:15px;top:1277px;width:92px;height:92px;background:linear-gradient(#c9b7a0,#7b6a58)}
.organizer-info{left:120px;top:1279px;font-size:13.5px;line-height:22px;color:#444;width:190px}
.organizer-info .name{font-size:16px;color:#222}
.organizer-text{left:15px;top:1385px;width:295px;font-size:12.5px;line-height:21px;color:#444}
.sort{left:21px;top:1522px;width:278px;height:37px;border:2px solid #bcc;border-radius:6px;font-size:12.5px;color:#555;padding:8px 42px;background:#fafafa}
.post-btn{left:21px;top:1613px;width:278px;height:42px;border-radius:6px;background:linear-gradient(var(--teal-light),var(--teal-dark));color:#fff;font-size:19px;display:flex;align-items:center;justify-content:center;box-shadow:0 2px 3px rgba(0,0,0,.3)}

.site-footer{left:35px;top:2327px;width:1145px;height:372px;background:linear-gradient(var(--teal-light),#2f6a62)}
.footer-title{font-size:19px;color:#fff}
.links{left:48px;top:70px;width:690px;display:grid;grid-template-columns:128px 165px 165px 200px;color:#fff;font-size:14px}
.links span{border-bottom:1px dotted rgba(255,255,255,.45);padding:8px 0 6px 4px;margin-right:12px}
.social{left:768px;top:65px;display:flex;gap:8px}
.social i{width:30px;height:30px;border-radius:50%;background:#fff;display:block}
.copyright{left:25px;top:249px;width:1095px;height:50px;background:rgba(0,0,0,.18);color:#fff;font-size:12px;padding:17px 18px}
</style>
</head>
<body>

<div class="top-bar"><span>EVENTS</span><span>NEWS EVENTS</span><span>SAVOR</span><span>EVENT WORLD ART SERIES</span><span>CITY EVENTS CALENDAR</span></div>

<div class="abs brand">Events</div>
<div class="abs slogan">your company slogan here</div>
<div class="abs account">
  <span><svg width="16" height="16" viewBox="0 0 16 16"><path d="M2 7h3v8H2zM6 7l3-6c1.5 0 2 1 2 2l-1 3h4c1 0 1.5 1 1.2 2l-1.5 5c-.3.8-1 1-1.7 1H6z" fill="#2f655d"/></svg>SIGN UP</span>
  <span><svg width="16" height="18" viewBox="0 0 16 18"><rect x="1" y="8" width="14" height="10" rx="1" fill="#2f655d"/><path d="M4 8V5a4 4 0 0 1 8 0v3" stroke="#2f655d" stroke-width="2" fill="none"/></svg>LOGIN</span>
  <span><svg width="22" height="18" viewBox="0 0 22 18"><circle cx="11" cy="5" r="5" fill="#2f655d"/><path d="M1 18c0-6 5-8 10-8s10 2 10 8z" fill="#2f655d"/></svg>MEMBER</span>
</div>
<div class="abs search"><div class="field">Enter Keyword here</div><div class="go">Go</div></div>

<nav class="abs main-nav"><a>MAIN</a><a>POPULAR</a><a>EVENTS</a><a>HELP</a><a>SUPPORT</a><a>CONTACT</a></nav>

<div class="abs hero" role="img" aria-label="Conference hall with stage screens and rows of seats under warm lighting"></div>
<div class="abs hero-shade"></div>
<div class="abs slider-arrow" style="left:26px">‹</div>
<div class="abs slider-arrow" style="left:1156px">›</div>

<div class="abs filter-bar">Date: <span class="pill" style="width:150px"></span>Category: <span class="pill" style="width:170px"></span>Show: <span class="pill" style="width:150px"></span><span class="go">GO</span></div>

<section class="abs event-list">
  <div class="abs total">Total Events 30</div>

  <article class="event" style="top:62px">
    <div class="thumb" role="img" aria-label="Winner holding a cash prize at a gaming event" style="background:linear-gradient(#1d2a4a,#5b6784 60%,#c9c6b4)"></div>
    <div class="event-body">
      <h3 class="event-title">Harbour Treasure Hunt on the Tramline</h3>
      <p class="event-desc">E-Commerce is a major progress in technology that has changed the way in which the customers now purchase information, products and the services. I</p>
      <div class="event-meta">20 March 2012 &nbsp;until &nbsp;20 April 2012<br>Any Tramline Station<br>Chicago, IL</div>
      <div class="share">Share With <i class="s1"></i><i class="s2"></i><i class="s3"></i></div>
    </div>
  </article>

  <article class="event" style="top:299px">
    <div class="thumb" role="img" aria-label="Laser light show over a crowd" style="background:linear-gradient(135deg,#05161a,#1f7a5c 50%,#0a2a30)"></div>
    <div class="event-body">
      <h3 class="event-title">18th Harbour Art Showcase</h3>
      <p class="event-desc">E-Commerce is a major progress in technology that has changed the way in which the customers now purchase information, products and the services. I</p>
      <div class="event-meta">20 March 2012 &nbsp;until &nbsp;20 April 2012<br>Any Tramline Station<br>Chicago, IL</div>
      <div class="share">Share With <i class="s1"></i><i class="s2"></i><i class="s3"></i></div>
    </div>
  </article>

  <div class="separator" style="top:511px"></div>

  <article class="event" style="top:558px">
    <div class="thumb" role="img" aria-label="Stage with presenters and purple screens" style="background:linear-gradient(#2a1030,#8a2a6a 50%,#3a1a28)"></div>
    <div class="event-body">
      <h3 class="event-title">The Permanent Exhibition</h3>
      <p class="event-desc">E-Commerce is a major progress in technology that has changed the way in which the customers now purchase information, products and the services. I</p>
      <div class="event-meta">20 March 2012 &nbsp;until &nbsp;20 April 2012<br>Any Tramline Station<br>Chicago, IL</div>
      <div class="share">Share With <i class="s1"></i><i class="s2"></i><i class="s3"></i></div>
    </div>
  </article>

  <div class="separator" style="top:766px"></div>

  <article class="event" style="top:793px">
    <div class="thumb" role="img" aria-label="Exhibition stage lit in magenta and blue" style="background:linear-gradient(#140a30,#8a1e8a 55%,#2a0a2a)"></div>
    <div class="event-body">
      <h3 class="event-title">Lantern Bay Exhibition</h3>
      <p class="event-desc">E-Commerce is a major progress in technology that has changed the way in which the customers now purchase information, products and the services. I</p>
      <div class="event-meta">20 March 2012 &nbsp;until &nbsp;20 April 2012<br>Any Tramline Station<br>Chicago, IL</div>
      <div class="share">Share With <i class="s1"></i><i class="s2"></i><i class="s3"></i></div>
    </div>
  </article>

  <article class="event" style="top:1030px">
    <div class="thumb" role="img" aria-label="Banquet hall with set tables in violet light" style="background:linear-gradient(#3a2a8a,#8a7ad0 55%,#d8d4ee)"></div>
    <div class="event-body" style="left:268px">
      <h3 class="event-title">Harbour Treasure Hunt on the Tramline</h3>
      <p class="event-desc">E-Commerce is a major progress in technology that has changed the way in which the customers now purchase information, products and the services. I</p>
      <div class="event-meta">20 March 2012 &nbsp;until &nbsp;20 April 2012<br>Any Tramline Station<br>Chicago, IL</div>
      <div class="share">Share With <i class="s1"></i><i class="s2"></i><i class="s3"></i></div>
    </div>
  </article>

  <div class="separator" style="top:1248px"></div>

  <article class="event" style="top:1295px">
    <div class="thumb" role="img" aria-label="Exhibition stage lit in magenta and blue" style="background:linear-gradient(#1a0a2a,#a02a9a 55%,#2a0a1a)"></div>
    <div class="event-body">
      <h3 class="event-title">Lantern Bay Exhibition</h3>
      <p class="event-desc">E-Commerce is a major progress in technology that has changed the way in which the customers now purchase information, products and the services. I</p>
      <div class="event-meta">20 March 2012 &nbsp;until &nbsp;20 April 2012<br>Any Tramline Station<br>Chicago, IL</div>
      <div class="share">Share With <i class="s1"></i><i class="s2"></i><i class="s3"></i></div>
    </div>
  </article>

  <div class="abs pager-line"></div>
  <div class="abs pager"><span class="current">1</span><span>2</span><span>3</span><span>4</span><span>5</span><span>6</span><span>7</span><span>8</span><span style="margin-left:8px">Next</span></div>
</section>

<aside class="abs sidebar">
  <div class="side-head" style="top:0">Popular Events</div>
  <div class="side-img" role="img" aria-label="Smiling man holding up cards on a stage" style="top:58px;background:linear-gradient(#1a2a8a,#5a4a9a 50%,#c88a4a)"></div>
  <div class="side-event" style="top:208px">
    <h4>Event Name here</h4>
    <div class="when">10 July to 20 Aug &nbsp;| &nbsp; Sydney &nbsp;NW</div>
    <p>Brightmere eSolutions is specialized in handling advanced web projects and the ongoing projects that require permanent maintenance and support .</p>
    <div class="more">learn more about this event ›</div>
  </div>

  <div class="side-head" style="top:408px">Related Events</div>
  <div class="edit-view" style="top:462px">Edit &nbsp;| &nbsp;View</div>
  <div class="side-img" role="img" aria-label="Evening party under large glowing globe lights" style="top:492px;background:radial-gradient(circle at 50% 40%,#9ab4ea,#2a46a8 60%,#0a1440)"></div>
  <div class="side-event" style="top:645px">
    <h4>Event Name here</h4>
    <div class="when">10 July to 20 Aug &nbsp;| &nbsp; Sydney &nbsp;NW</div>
    <p>Brightmere eSolutions is specialized in handling advanced web projects and the ongoing projects that require permanent maintenance and support .</p>
    <div class="more">learn more about this event ›</div>
  </div>
  <div style="position:absolute;left:10px;top:828px;width:304px;border-top:1px dashed #aaa"></div>
  <div class="edit-view" style="top:838px">Edit &nbsp;| &nbsp;View</div>
  <div class="side-img" role="img" aria-label="Evening party under large glowing globe lights" style="top:868px;background:radial-gradient(circle at 50% 40%,#9ab4ea,#2a46a8 60%,#0a1440)"></div>
  <div class="side-event" style="top:1020px">
    <h4>Event Name here</h4>
    <div class="when">10 July to 20 Aug &nbsp;| &nbsp; Sydney &nbsp;NW</div>
    <p>Brightmere eSolutions is specialized in handling advanced web projects and the ongoing projects that require permanent maintenance and support .</p>
    <div class="more">learn more about this event ›</div>
  </div>

  <div class="side-head" style="top:1226px">Event Organizer</div>
  <div class="abs organizer-photo" role="img" aria-label="Organizer portrait photo"></div>
  <div class="abs organizer-info">The best best practices?<br><span class="name">Harlowe's</span><br>Posted by harlowe on July 6, 2012 at 10:35am</div>
  <div class="abs organizer-text">Brightmere eSolutions is specialized in handling advanced web projects and the ongoing projects that require permanent maintenance and support .</div>
  <div class="abs sort">Sort By :<svg class="abs" style="right:12px;top:13px" width="10" height="7" viewBox="0 0 10 7"><path d="M0 0h10L5 7z" fill="#3f7f76"/></svg></div>
  <div class="abs post-btn">POST AN EVENT</div>
</aside>

<footer class="abs site-footer">
  <div class="abs footer-title" style="left:48px;top:30px">Quick Links</div>
  <div class="abs links">
    <span>Hom page</span><span>Login</span><span>Support</span><span>Term &amp; Conditions of Use</span>
    <span>Events</span><span>FAQ</span><span>Add Events</span><span>Privacy Policy</span>
    <span>Popular</span><span>Login</span><span>Speical Events</span><span>Help</span>
    <span>News</span><span>Forgot Password</span><span>Contact info</span><span style="border:none"></span>
  </div>
  <div class="abs footer-title" style="left:763px;top:25px">Connect with Us</div>
  <div class="abs social"><i></i><i></i><i></i></div>
  <div class="abs copyright">© 2012 Company Name &nbsp;| &nbsp;All right reserved &nbsp;| &nbsp;Policy Privacy</div>
</footer>

</body>
</html>
```